Website Redesign using existing images, copy etc.

I'm looking for a website redesign/refresh of my current WordPress website. I would like to utilize the same photography, a new photo viewer, and an overall refresh of the entire design. This will need to be WordPress with simple accessibility to make changes as we add additional properties and make updates. We auction luxury real estate and luxury yachts for non-distressed sellers. It needs to be simple, luxurious and with ease of use for both web and especially mobile. www.BrindleHarrow.com

```html
<!DOCTYPE html>
<html lang="en">
<head>
<meta charset="utf-8">
<title>Brindle Harrow — Real Estate &amp; Yachts</title>
<link href="https://fonts.googleapis.com/css2?family=Cormorant+Garamond:wght@500;600&family=Montserrat:wght@400;500;600;700&display=swap" rel="stylesheet">
<style>
:root{
  --gold:#ab9b78;
  --gold-deep:#96845f;
  --sand:#e8e3da;
  --ink:#1d1d1d;
  --text:#3a3a3a;
  --white:#ffffff;
  --black:#000000;
  --night:#2c3640;
}
*{margin:0;padding:0;box-sizing:border-box}
html,body{width:1200px;height:4210px;overflow:hidden}
body{position:relative;background:var(--white);font-family:'Montserrat',sans-serif;color:var(--text)}
.abs{position:absolute}
.serif{font-family:'Cormorant Garamond',serif}

/* hero */
.hero{left:0;top:0;width:1200px;height:730px}
.hero-photo{position:absolute;inset:0}
.nav{top:62px;left:0;width:1200px;height:40px}
.nav a{position:absolute;top:10px;color:var(--white);font-size:17px;font-weight:600;letter-spacing:1px;text-decoration:none}
.nav-mark{position:absolute;left:550px;top:-32px;width:100px;height:100px;border:3px solid var(--white);border-radius:50%;display:flex;align-items:center;justify-content:center;color:var(--white);font-family:'Cormorant Garamond',serif;font-size:16px;font-weight:600;letter-spacing:1px}
.hero-title{top:256px;left:0;width:1200px;text-align:center;color:var(--white);font-family:'Cormorant Garamond',serif;font-size:50px;font-weight:500;letter-spacing:22px}
.hero-sub{top:372px;left:0;width:1200px;text-align:center;color:var(--white);font-size:25px;font-weight:600;letter-spacing:.5px}
.pill{display:flex;align-items:center;justify-content:center;background:var(--gold);color:var(--white);border-radius:40px;font-weight:600;letter-spacing:1px;text-decoration:none}
.hero-btn{top:463px;height:70px;width:482px;font-size:24px}
.medallion{left:540px;top:656px;width:120px;height:120px;border-radius:50%;background:var(--gold);display:flex;align-items:center;justify-content:center}
.medallion span{width:96px;height:96px;border:3px solid var(--white);border-radius:50%}

/* headings */
.section-title{left:0;width:1200px;text-align:center;font-family:'Cormorant Garamond',serif;font-weight:600;color:var(--ink);font-size:36px;letter-spacing:1px}

/* intro */
.intro-visual{left:115px;top:958px;width:455px;height:455px;border-radius:50%}
.eyebrow{color:var(--gold);font-weight:600;font-size:23px;letter-spacing:.5px}
.body-copy{font-size:21px;line-height:41px;letter-spacing:.6px;color:var(--text)}
.intro-copy{left:605px;top:1048px;width:490px;text-align:justify}

/* featured */
.press-card{top:1588px;width:234px;height:174px;background:var(--white);border-radius:12px;box-shadow:0 2px 8px rgba(0,0,0,.22);display:flex;align-items:center;justify-content:center;text-align:center;color:#7a7a7a;font-family:'Cormorant Garamond',serif;font-weight:600;font-size:27px;line-height:1.1;padding:0 14px}
.press-card.is-active{background:#e4e4e4}
.dots{top:1830px;left:548px;display:flex;gap:12px;align-items:center}
.dots i{display:block;width:10px;height:10px;border-radius:50%;background:var(--gold)}
.dots i:first-child{width:14px;height:14px}

/* about */
.about{left:0;top:1942px;width:1200px;height:710px;background:var(--sand)}
.founder-name{right:628px;top:2088px;text-align:right}
.founder-name small{font-size:19px}
.about-copy{right:628px;top:2147px;width:440px;text-align:right}
.learn-btn{left:302px;top:2475px;width:270px;height:81px;font-size:26px}
.portrait{left:600px;top:2053px;width:485px;height:530px;border-radius:50%}

/* sold */
.sold-circle{top:2847px;width:314px;height:314px;border-radius:50%;overflow:hidden}
.sold-overlay{position:absolute;inset:0;background:rgba(30,30,30,.62);display:flex;flex-direction:column;align-items:center;justify-content:center;color:var(--white);text-align:center}
.sold-overlay h3{font-family:'Cormorant Garamond',serif;font-weight:600;font-size:36px;line-height:54px;letter-spacing:2px}
.sold-overlay p{font-size:20px;font-weight:600;line-height:41px;margin-top:6px}
.arrow{top:3205px;width:60px;height:60px;border-radius:50%;background:var(--gold);display:flex;align-items:center;justify-content:center}

/* signup */
.signup{left:0;top:3360px;width:1200px;height:377px;background:var(--gold)}
.signup-title{top:3402px;font-size:35px;letter-spacing:3px;color:#1a1a1a}
.field{top:3497px;width:413px;height:66px;background:var(--white);border-radius:6px;display:flex;align-items:center;padding-left:27px;font-size:20px;font-weight:600;color:#333}
.submit{left:498px;top:3615px;width:206px;height:72px;border-radius:40px;background:var(--white);color:#111;font-size:25px;font-weight:700;letter-spacing:1.5px;display:flex;align-items:center;justify-content:center}

/* footer */
.footer{left:0;top:3737px;width:1200px;height:473px;background:var(--black)}
.badge{left:562px;top:3800px;width:76px;height:76px;border:3px solid var(--gold-deep);border-radius:50%}
.footer-nav{top:3956px;left:0;width:1200px;display:flex;justify-content:center;gap:31px}
.footer-nav a{color:var(--white);font-size:20px;font-weight:600;text-decoration:none;letter-spacing:.3px}
.social{top:4027px;width:70px;height:70px;border-radius:50%;background:var(--white);border:3px solid #9a9a9a;display:flex;align-items:center;justify-content:center;color:var(--black);font-size:15px;font-weight:700}
.copyright{top:4145px;left:0;width:1200px;text-align:center;color:var(--white);font-size:16px;font-weight:600;letter-spacing:.5px}
</style>
</head>
<body>

<section class="abs hero">
  <div class="hero-photo" role="img" aria-label="Photograph of a luxury estate at dusk with a lit pool and palms" style="background:linear-gradient(180deg,#2f3c4a 0%,#4a4a40 30%,#6b5b44 48%,#2f4c58 68%,#5a6666 100%)"></div>
  <svg class="abs" style="left:0;top:600px" width="1200" height="130" viewBox="0 0 1200 130">
    <path d="M0 44 Q600 190 1200 44 L1200 130 L0 130 Z" fill="#ffffff"/>
    <path d="M0 44 Q600 190 1200 44 L1200 56 Q600 200 0 56 Z" fill="#9a8966"/>
  </svg>
  <nav class="abs nav">
    <a href="#" style="left:368px">BUY</a>
    <a href="#" style="left:470px">SELL</a>
    <span class="nav-mark">BH</span>
    <a href="#" style="left:690px">ABOUT</a>
    <a href="#" style="left:820px">CONTACT</a>
  </nav>
  <h1 class="abs hero-title">BRINDLE HARROW</h1>
  <p class="abs hero-sub">REAL ESTATE &amp; YACHTS</p>
  <a class="abs pill hero-btn" href="#" style="left:98px">BROWSE UPCOMING AUCTIONS</a>
  <a class="abs pill hero-btn" href="#" style="left:620px">BROWSE PAST SUCCESSES</a>
</section>
<div class="abs medallion"><span></span></div>

<h2 class="abs section-title" style="top:855px">Over One Billion Dollars of Auctions Marketed</h2>
<div class="abs intro-visual" role="img" aria-label="Yacht deck and seascape photograph framed in a circle" style="background:linear-gradient(160deg,#8cc6d2 0%,#d8dfe0 40%,#6a8d99 70%,#1c2326 100%)"></div>
<p class="abs eyebrow" style="left:604px;top:992px">REAL ESTATE &amp; YACHTS</p>
<p class="abs body-copy intro-copy">The experience of hearing the auctioneer’s final proclamation of “SOLD!” is unparalleled. Whether it’s the initial meeting with the seller at their estate or yacht, or the triumphant raising of the paddle by the winning buyer, we relish every moment of the process and the ensuing festivities. We’re confident that you will, too.</p>

<h2 class="abs section-title" style="top:1498px">As Featured In</h2>
<div class="abs press-card" style="left:106px">The Harbor Ledger</div>
<div class="abs press-card" style="left:356px">Meridian</div>
<div class="abs press-card is-active" style="left:606px">Coastline Business</div>
<div class="abs press-card" style="left:856px">Tidewater News</div>
<div class="abs dots"><i></i><i></i><i></i><i></i><i></i></div>

<section class="abs about"></section>
<h2 class="abs section-title" style="top:1986px">About Us</h2>
<p class="abs eyebrow founder-name">MARTIN CALLOWAY - <small>CEO &amp; FOUNDER</small></p>
<p class="abs body-copy about-copy">Have you ever experienced a sense of purpose in your life? I consider myself fortunate enough to have felt it not once, but twice. At the age of 18, I realized my first calling as a Paratrooper in the US Army. Although I enjoyed being a Paratrooper, I knew it couldn’t</p>
<a class="abs pill learn-btn" href="#">LEARN MORE</a>
<div class="abs portrait" role="img" aria-label="Portrait photograph of the founder in a blue blazer outdoors" style="background:linear-gradient(170deg,#9fb7a4 0%,#d9c9b2 35%,#40587a 70%,#273a55 100%)"></div>

<h2 class="abs section-title" style="top:2738px">Sold by Brindle Harrow</h2>
<div class="abs sold-circle" style="left:113px" role="img" aria-label="Photograph of a Mediterranean estate with palms and a brick driveway at sunset"><div style="position:absolute;inset:0;background:linear-gradient(180deg,#c99a8a 0%,#d8c6a8 35%,#3f5a38 70%,#8c6460 100%)"></div></div>
<div class="abs sold-circle" style="left:443px" role="img" aria-label="Photograph of an estate interior, sold prior to auction"><div style="position:absolute;inset:0;background:linear-gradient(180deg,#b7a68a,#6a5c48)"></div>
  <div class="sold-overlay"><h3>SOLD PRIOR TO<br>AUCTION</h3><p>2718 Heron Point Ln<br>Marlow | FL</p></div>
</div>
<div class="abs sold-circle" style="left:770px" role="img" aria-label="Photograph of a motor yacht on the water"><div style="position:absolute;inset:0;background:linear-gradient(180deg,#6fa3d8 0%,#b9d2e6 40%,#1f2a44 65%,#8a99a8 100%)"></div></div>
<div class="abs arrow" style="left:522px"><svg width="22" height="22" viewBox="0 0 22 22"><path d="M14 3 L6 11 L14 19" fill="none" stroke="#111" stroke-width="3"/></svg></div>
<div class="abs arrow" style="left:616px"><svg width="22" height="22" viewBox="0 0 22 22"><path d="M8 3 L16 11 L8 19" fill="none" stroke="#111" stroke-width="3"/></svg></div>

<section class="abs signup"></section>
<h2 class="abs section-title signup-title">SIGN UP FOR BRINDLE ALERTS</h2>
<div class="abs field" style="left:175px">Name</div>
<div class="abs field" style="left:612px;padding-left:31px">Email Address</div>
<div class="abs submit">SUBMIT</div>

<footer class="abs footer"></footer>
<div class="abs badge" role="img" aria-label="Veteran owned business badge"></div>
<nav class="abs footer-nav">
  <a href="#">HOME</a><a href="#">BUY</a><a href="#">SELL</a><a href="#">ABOUT</a><a href="#">BLOG</a><a href="#">CONTACT</a><a href="#">TERMS OF SERVICE</a><a href="#">PRIVACY POLICY</a>
</nav>
<div class="abs social" style="left:425px">Feed</div>
<div class="abs social" style="left:519px">Snap</div>
<div class="abs social" style="left:612px">Link</div>
<div class="abs social" style="left:706px">Post</div>
<p class="abs copyright">@2023 COPYRIGHTS. BRINDLE HARROW. ALL RIGHTS RESERVED.</p>

</body>
</html>
```